A private security company called "Tavron Security Services Ltd"

Hello everybody,

We need a web page for a company based in NZ. It is mainly an informative website so it would be wonderful if the designer puts their absolute best into making it a website that I would really appreciate. The website needs to show professionalism and also needs to make our web surfers find the information they need in a click. the company's colour is black and silver, and if those two colours could be integrated into the website it would be absolutely lovely. Please do contact me for any information.

Sincerely,
Dorian Vaskel

Industry/Entity Type

Security

```html
<!DOCTYPE html>
<html lang="en">
<head>
<meta charset="utf-8">
<title>Tavron Security Services Ltd</title>
<link href="https://fonts.googleapis.com/css2?family=Montserrat:wght@400;600;700&family=Open+Sans:wght@400;600&display=swap" rel="stylesheet">
<style>
:root{
  --black:#000;
  --ink:#1a1a1a;
  --grey-text:#6a6a6a;
  --silver:#d6d6d6;
  --light:#efefef;
  --white:#fff;
  --footer-text:#9a9a9a;
  --rule:#2a2a2a;
}
*{box-sizing:border-box;margin:0;padding:0}
html,body{width:947px;height:1200px;overflow:hidden;background:var(--white)}
body{position:relative;font-family:"Open Sans",Arial,sans-serif;color:var(--ink)}
.abs{position:absolute}

/* header */
.site-header{left:0;top:0;width:947px;height:118px;background:linear-gradient(#fff,#f1f1f1);border-bottom:1px solid #cfcfcf}
.brand{left:87px;top:48px;display:flex;align-items:center;gap:8px;font-family:"Open Sans",Arial,sans-serif;font-weight:600;font-size:15px;line-height:1.1;color:var(--black)}
.brand-mark{width:14px;height:14px;border-radius:50%;background:var(--black)}
.call-box{left:686px;top:0;width:174px;height:27px;background:var(--silver);border-radius:0 0 3px 3px;font-family:"Montserrat",Arial,sans-serif;font-size:15px;line-height:27px;text-align:center;color:var(--ink)}
.call-box b{font-weight:600}
.main-nav{left:0;top:91px;width:947px;height:27px}
.main-nav a{position:absolute;top:0;font-size:11.2px;color:#333;text-decoration:none;white-space:nowrap}
.main-nav a.active{font-weight:600;color:var(--black)}
.nav-underline{left:385px;top:115px;width:43px;height:3px;background:#333}
.search-icon{left:836px;top:92px}

/* hero */
.hero{left:0;top:118px;width:947px;height:350px;background:linear-gradient(100deg,#c9d6df 0%,#e9eef2 35%,#d8e2ea 60%,#b9c9d6 100%)}
.hero-title{left:88px;top:240px;font-family:"Montserrat",Arial,sans-serif;font-size:21px;font-weight:400;letter-spacing:-.5px;color:#111}
.hero-title strong{font-weight:600}
.hero-text{left:89px;top:283px;width:462px;font-family:"Montserrat",Arial,sans-serif;font-size:9.6px;line-height:13px;letter-spacing:-.1px;color:#111}

/* service tabs */
.service-tabs{left:0;top:468px;width:947px;height:37px;background:linear-gradient(#1e1e1e,#000)}
.tab{position:absolute;top:0;height:37px;display:flex;align-items:center;font-family:"Montserrat",Arial,sans-serif;font-weight:600;font-size:10.5px;line-height:12px;color:var(--white);text-transform:uppercase}
.tab.current{background:var(--silver);color:#111}

/* intro */
.intro{left:0;top:505px;width:947px;height:167px;background:var(--light)}
.intro p{position:absolute;left:104px;top:43px;width:740px;text-align:center;font-family:"Montserrat",Arial,sans-serif;font-size:11px;line-height:15px;letter-spacing:-.15px;color:var(--grey-text)}

/* features */
.feature{top:722px;width:200px;text-align:center}
.feature-icon{display:block;margin:0 auto}
.feature h3{margin-top:14px;font-size:12.5px;font-weight:600;color:#111;text-transform:uppercase}
.feature p{margin:6px auto 0;width:132px;font-size:9.5px;line-height:12px;color:var(--grey-text)}
.feature .more{position:absolute;left:0;width:200px;top:225px;font-size:10px;color:#111;text-decoration:underline}

/* footer */
.site-footer{left:0;top:991px;width:947px;height:209px;background:var(--black);color:var(--footer-text);font-size:11px;line-height:16px}
.footer-col{top:23px}
.footer-col h4{font-weight:400;font-size:12.5px;color:var(--white);padding-bottom:9px;border-bottom:1px solid var(--rule);width:184px;margin-bottom:17px}
.socials{display:flex;gap:4px;margin-top:7px}
.socials span{width:19px;height:19px;border-radius:3px}
.subscribe-form{display:flex;margin-top:8px}
.subscribe-form .field{width:131px;height:29px;background:var(--white);color:#aaa;font-size:11px;line-height:29px;padding-left:8px}
.subscribe-form .btn{width:38px;height:29px;background:#111;border:1px solid #555;color:var(--white);font-size:12px;line-height:27px;text-align:center}
.footer-rule{left:103px;top:172px;width:754px;height:1px;background:var(--rule)}
.copyright{left:0;top:184px;width:947px;text-align:center;color:#ddd;font-size:10.5px}
</style>
</head>
<body>

<header class="site-header abs">
  <div class="brand abs"><span class="brand-mark"></span><span>Tavron<br>Security Services Ltd.</span></div>
  <div class="call-box abs">Call: <b>240 6613 572</b></div>
  <nav class="main-nav abs">
    <a class="active" style="left:390px">HOME</a>
    <a style="left:449px">About Us</a>
    <a style="left:518px">Security Services</a>
    <a style="left:624px">Why Us</a>
    <a style="left:685px">Testimonials</a>
    <a style="left:771px">Contct Us</a>
  </nav>
  <svg class="search-icon abs" width="15" height="15" viewBox="0 0 15 15"><circle cx="6" cy="6" r="4.3" fill="none" stroke="#666" stroke-width="2"/><line x1="9.2" y1="9.2" x2="13.5" y2="13.5" stroke="#666" stroke-width="2.4" stroke-linecap="round"/></svg>
</header>
<div class="nav-underline abs"></div>

<section class="hero abs" role="img" aria-label="Photo of two security cameras on a metal pole against a cloudy sky"></section>
<h1 class="hero-title abs"><strong>Newzealand’s Best</strong> Security Company</h1>
<p class="hero-text abs">It is a long established fact that a reader will be distracted by the readable content of a page when looking at its layout. The point of using Lorem Ipsum is that it has a more-or-less normal distribution of lettersas opposed to using 'Content here, content here', making it look like readable English.</p>

<nav class="service-tabs abs">
  <div class="tab" style="left:92px">Security Guards</div>
  <div class="tab current" style="left:255px;width:195px;padding-left:34px">Commercial Security<br>Systems</div>
  <div class="tab" style="left:505px">Commercial Alarm<br>Monitoring &amp; Response</div>
  <div class="tab" style="left:715px">Specialized Security</div>
</nav>

<section class="intro abs">
  <p>It is a long established fact that a reader will be distracted by the readable content of a page when looking at its layout. The point of using Lorem Ipsum is that it has a more-or-less normal distribution of letters, as opposed to using 'Content here, content here', making it look like readable English. Many desktop publishing packages and web page editors now use Lorem Ipsum as their default model text, and a search for 'lorem ipsum' will uncover many web sites still in their infancy. Various versions have evolved over the years, sometimes by accident, sometimes on purpose (injected humour and the like).</p>
</section>

<article class="feature abs" style="left:73px">
  <svg class="feature-icon" width="86" height="86" viewBox="0 0 86 86"><circle cx="43" cy="43" r="43" fill="#000"/><g fill="#fff"><rect x="24" y="35" width="34" height="13" rx="2" transform="rotate(-22 41 41)"/><rect x="44" y="48" width="8" height="6"/><rect x="54" y="44" width="4" height="16"/></g></svg>
  <h3>Security Cameras</h3>
  <p>It is a long established fact that a reader will be distracted by the readable content of a page when looking at its layout. The point of using Lorem Ipsum</p>
  <a class="more">READ MORE</a>
</article>
<article class="feature abs" style="left:269px">
  <svg class="feature-icon" width="86" height="86" viewBox="0 0 86 86"><circle cx="43" cy="43" r="43" fill="#000"/><g fill="none" stroke="#fff" stroke-width="3"><rect x="28" y="30" width="28" height="14" rx="3" transform="rotate(28 42 37)"/><rect x="44" y="44" width="14" height="12" rx="2"/><line x1="32" y1="44" x2="32" y2="58"/></g><circle cx="51" cy="50" r="2.5" fill="#fff"/></svg>
  <h3>CCTV Cameras</h3>
  <p>It is a long established fact that a reader will be distracted by the readable content of a page when looking at its layout. The point of using Lorem Ipsum</p>
  <a class="more">READ MORE</a>
</article>
<article class="feature abs" style="left:473px">
  <svg class="feature-icon" width="86" height="86" viewBox="0 0 86 86"><circle cx="43" cy="43" r="43" fill="#000"/><path d="M43 25 L60 31 C60 46 54 56 43 62 C32 56 26 46 26 31 Z" fill="none" stroke="#fff" stroke-width="3"/><path d="M43 31 L54 35 C54 45 50 52 43 56 Z" fill="#fff"/></svg>
  <h3>Security</h3>
  <p>It is a long established fact that a reader will be distracted by the readable content of a page when looking at its layout. The point of using Lorem Ipsum</p>
  <a class="more">READ MORE</a>
</article>
<article class="feature abs" style="left:680px">
  <svg class="feature-icon" width="86" height="86" viewBox="0 0 86 86"><circle cx="43" cy="43" r="43" fill="#000"/><path d="M40 24 L54 29 C54 42 50 51 40 57 C30 51 26 42 26 29 Z" fill="none" stroke="#fff" stroke-width="3"/><path d="M40 29 L40 52 C33 48 31 41 31 32 Z" fill="#fff"/><circle cx="53" cy="52" r="9" fill="#fff"/><path d="M48.5 52 L52 55.5 L58 48.5" fill="none" stroke="#000" stroke-width="2.4"/></svg>
  <h3>Perosnal Security</h3>
  <p>It is a long established fact that a reader will be distracted by the readable content of a page when looking at its layout. The point of using Lorem Ipsum</p>
  <a class="more">READ MORE</a>
</article>

<footer class="site-footer abs">
  <div class="footer-col abs" style="left:99px">
    <h4>CONTACT US</h4>
    <p>Harbourview, HV 48213<br>214 Kestrel Street<br>phone: +0 02471 06233 0918<br>Fax: +5 611 42 7083<br>Email: hello@tavronsecurity.nz</p>
  </div>
  <div class="footer-col abs" style="left:339px">
    <h4>GO SOCIAL</h4>
    <p>Stay in touch with us:</p>
    <div class="socials">
      <span style="background:#3b5a9a"></span><span style="background:#2aa3e0"></span><span style="background:#d23a2a"></span><span style="background:#c8232c"></span><span style="background:#8a6a50"></span><span style="background:#f07a1a"></span>
    </div>
  </div>
  <div class="footer-col abs" style="left:645px">
    <h4>SUBSCRIBE</h4>
    <p>Enter your e-mail below to subscribe to our<br>free newsletter.<br>We promise not to bother you often!</p>
    <div class="subscribe-form"><div class="field">Enter Email</div><div class="btn">OK</div></div>
  </div>
  <div class="footer-rule abs"></div>
  <p class="copyright abs">© Tavron Security Services 2014. Privacy Policy &nbsp;|&nbsp; Terms of Service</p>
</footer>

</body>
</html>
```